New Flyer for a Revamped Brand!

Hearthwild Pantry's vision is to give our customers their lives back, so they can spend more time dancing in their living rooms! To live your best life you need your health and your time, and with Hearthwild Pantry's pre-packaged, totally healthy (no gluten, no grains, no sugar), meals delivered straight to your door you can spend your time living a life you love!

We have just celebrated our first birthday, and in line with our newly stated vision, we would like to create some new collateral that is in line with this - starting with flyers!

I have attached our logo, and some images of our meals. Our website is www.hearthwildpantry-example.com.au and our homepage outlines the what, how and why.

We are looking for a flyer that both describes what we do, and captures our vision for health, time, and happiness.

Reason: All of the designs seem to be coming back as A4, where as a flyer should be DL sized. Please amend to DL.

Target Market(s)

Used in a letterbox drop in high income areas, as well as to hand out at health and fitness events

Industry/Entity Type

Kitchen

Requirements
Must have
• E: info@hearthwildpantry-example.com.au
• W: www.hearthwildpantry-example.com.au
• P: 0491 562 317
• FB: facebook.com/hearthwildpantryoz
• Insta: instagram.com/hearthwildpantryoz

```html
<!DOCTYPE html>
<html lang="en">
<head>
<meta charset="utf-8">
<title>Hearthwild Pantry — DL Flyer</title>
<link rel="stylesheet" href="https://fonts.googleapis.com/css2?family=Crimson+Pro:wght@400;700&family=Raleway:wght@300;400;500&display=swap">
<style>
  :root {
    --paper: #ffffff;
    --wine: #7e0c10;
    --gold: #f7b71d;
    --frame: #ffffff;
    --ink-light: #f3eaea;
    --leaf: #7fb53a;
    --caption: #222222;
  }
  * { box-sizing: border-box; margin: 0; padding: 0; }
  html, body { width: 772px; height: 1200px; overflow: hidden; background: var(--paper); }
  .canvas { position: relative; width: 772px; height: 1200px; background: var(--paper); }

  /* DL format: 99 x 210 mm */
  .flyer {
    position: absolute; left: 128px; top: 42px; width: 515px; height: 1092px;
    background: var(--wine); overflow: hidden;
  }
  .snapshot {
    position: absolute; background: var(--frame); padding: 10px;
    box-shadow: 5px 7px 11px rgba(0,0,0,.45);
    transform: translate(-50%, -50%) rotate(var(--tilt));
  }
  .snapshot .meal { display: block; width: 100%; height: 100%; }
  .meal--bowl    { background: linear-gradient(135deg, #d9d4c8, #8b7a4d 55%, #c9a24a); }
  .meal--pork    { background: linear-gradient(160deg, #e8e3db, #6d2a17 45%, #e6c98f 75%, #d9803a); }
  .meal--rissoles{ background: linear-gradient(180deg, #f2efea, #7a3a22 35%, #d9b86a 65%, #7aa83a); }
  .meal--stirfry { background: linear-gradient(140deg, #8c4a7a, #c8854a 45%, #b93224 70%, #e6d7c0); }
  .meal--salmon  { background: linear-gradient(150deg, #eef0ef, #e6a98a 45%, #d96f2a 70%, #6e8f3a); }
  .meal--tray    { background: linear-gradient(160deg, #5a3a2e, #b54a4a 40%, #d99a3a 70%, #6a4a2e); }

  .headline {
    position: absolute; left: 0; right: 0; top: 440px; text-align: center;
    font-family: "Crimson Pro", Georgia, serif; font-weight: 700;
    font-size: 46px; letter-spacing: -0.4px; color: var(--gold); line-height: 1;
  }
  .offer {
    position: absolute; left: 30px; right: 30px; top: 500px; text-align: center;
    font-family: "Raleway", Arial, sans-serif; font-weight: 500;
    font-size: 16px; line-height: 22px; color: var(--ink-light);
  }
  .brand {
    position: absolute; left: 22px; top: 580px; width: 90px;
    display: flex; flex-direction: column; align-items: center; gap: 7px;
  }
  .brand__mark { width: 20px; height: 20px; background: var(--leaf); }
  .brand__name {
    font-family: "Raleway", Arial, sans-serif; font-weight: 400;
    font-size: 15px; line-height: 1.15; color: var(--ink-light); text-align: center;
  }
  .contacts {
    position: absolute; left: 124px; top: 578px;
    font-family: "Raleway", Arial, sans-serif; font-weight: 300;
    font-size: 13.5px; line-height: 18px; color: var(--ink-light);
    display: grid; grid-template-columns: 72px auto;
  }
  .caption {
    position: absolute; left: 0; right: 0; top: 1162px; text-align: center;
    font-family: "Crimson Pro", Georgia, serif; font-weight: 400;
    font-size: 15px; color: var(--caption);
  }
</style>
</head>
<body>
<div class="canvas">
  <section class="flyer">
    <figure class="snapshot" style="left:150px; top:170px; width:210px; height:150px; --tilt:-13deg">
      <span class="meal meal--bowl" role="img" aria-label="Bowl of shredded chicken and vegetables with a lemon wedge"></span>
    </figure>
    <figure class="snapshot" style="left:365px; top:160px; width:205px; height:165px; --tilt:12deg">
      <span class="meal meal--pork" role="img" aria-label="Pork with caramelised onion, sauerkraut and sweet potato mash"></span>
    </figure>
    <figure class="snapshot" style="left:258px; top:330px; width:230px; height:155px; --tilt:3deg">
      <span class="meal meal--rissoles" role="img" aria-label="Meat rissoles on cauliflower rice with snow peas and lemon"></span>
    </figure>

    <h1 class="headline">Take your life back</h1>
    <p class="offer">Healthy pre-packaged meals delivered to your door.<br>No gluten · no grains · no sugar</p>

    <div class="brand">
      <span class="brand__mark"></span>
      <span class="brand__name">Hearthwild Pantry</span>
    </div>

    <dl class="contacts">
      <dt>Email:</dt><dd>info@hearthwildpantry-example.com.au</dd>
      <dt>Website:</dt><dd>www.hearthwildpantry-example.com.au</dd>
      <dt>Phone:</dt><dd>0491 562 317</dd>
      <dt>FB page:</dt><dd>facebook.com/hearthwildpantryoz</dd>
      <dt>Instagram:</dt><dd>instagram.com/hearthwildpantryoz</dd>
    </dl>

    <figure class="snapshot" style="left:150px; top:820px; width:190px; height:185px; --tilt:-15deg">
      <span class="meal meal--stirfry" role="img" aria-label="Chicken stir-fry with capsicum and purple slaw"></span>
    </figure>
    <figure class="snapshot" style="left:375px; top:805px; width:200px; height:150px; --tilt:12deg">
      <span class="meal meal--salmon" role="img" aria-label="Salmon fillets with mash, carrots and green beans"></span>
    </figure>
    <figure class="snapshot" style="left:270px; top:975px; width:215px; height:150px; --tilt:-3deg">
      <span class="meal meal--tray" role="img" aria-label="Tray bake of roasted pumpkin, beetroot and vegetables"></span>
    </figure>
  </section>
  <p class="caption">Size: DL 99 x 210 mm</p>
</div>
</body>
</html>
```